Automotive component supplier needs a business card design

We need a business card design for our company called Velran Global Components Ltd based in the UK. We are a supplier of interior and exterior components to premium car manufacturers such as Corvel Ashby, Hadley Fenn, Marquist and Tavarelli. We would like to see a modern business card design that uses the colour blue.

Target Market(s)

Premium automotive car manufacturers.

Industry/Entity Type

Automotive

Contact Information for Business Card

Company Name : Velran Global Components Limited
Address: 17 Marlow Yard, Upper Heath, Warwick, CV31 8QL, United Kingdom
Web Address : www.velrancomponents-example.co.uk

Font styles to use
Other font styles liked:
• Helvetica

Colors
3176b5
0255a3
85acd3
cfdeed
cee9f5
85cae6
34a6d7
0692cd
9bcb3c

Requirements
Must have
• Clear company logo and a mixture of blue colours.
Nice to have
• A high quality modern image.
Should not have
• Multiple colours.

```html
<!DOCTYPE html>
<html lang="en">
<head>
<meta charset="utf-8">
<title>Velran Global Components – Business Card</title>
<link href="https://fonts.googleapis.com/css2?family=Arimo:wght@400;700&display=swap" rel="stylesheet">
<style>
  :root {
    --stage: #2e2e2e;
    --brand-blue: #0a7fc2;
    --back-blue: #1189cc;
    --accent-green: #8cc63f;
    --text-grey: #6b6b6b;
    --card-light: #ffffff;
    --card-shade: #e4e4e4;
    --white: #ffffff;
  }
  * { margin: 0; padding: 0; box-sizing: border-box; }
  html, body {
    width: 1200px; height: 965px; overflow: hidden;
    background: var(--stage);
    font-family: "Arimo", Helvetica, Arial, sans-serif;
  }
  .canvas { position: relative; width: 1200px; height: 965px; }

  .card {
    position: absolute; left: 246px; width: 710px; height: 402px;
    box-shadow: 0 3px 10px rgba(0,0,0,0.45);
  }
  .card-front {
    top: 60px;
    background: radial-gradient(ellipse at 40% 35%, var(--card-light) 0%, #f6f6f6 55%, var(--card-shade) 100%);
  }
  .card-back { top: 504px; background: var(--back-blue); overflow: hidden; }

  /* Front: wordmark */
  .front-wordmark {
    position: absolute; left: 52px; top: 52px;
    display: flex; align-items: center; gap: 12px;
  }
  .front-wordmark .mark-square {
    width: 14px; height: 14px; background: var(--accent-green);
  }
  .front-wordmark .mark-name {
    color: var(--brand-blue); font-weight: 700; line-height: 1;
  }
  .mark-name .line-main { display: block; font-size: 52px; letter-spacing: 2px; }
  .mark-name .line-sub { display: block; font-size: 17px; letter-spacing: 2.4px; margin-top: 8px; }

  /* Front: person */
  .contact-block { position: absolute; left: 404px; top: 150px; }
  .person-name {
    color: var(--brand-blue); font-weight: 700; font-size: 22px; letter-spacing: 0.3px;
  }
  .person-title { color: var(--accent-green); font-size: 16px; margin-top: 3px; }

  .contact-list { list-style: none; margin-top: 36px; }
  .contact-list li {
    display: flex; align-items: center; gap: 10px;
    color: var(--text-grey); font-size: 14.5px; line-height: 20.5px;
    white-space: nowrap;
  }
  .contact-list svg { width: 16px; height: 16px; flex: none; }

  .address {
    margin-top: 26px; color: var(--text-grey); font-size: 14.5px; line-height: 20.5px;
    font-style: normal; white-space: nowrap;
  }

  .front-web {
    position: absolute; left: 52px; top: 352px;
    color: var(--text-grey); font-size: 14.5px; white-space: nowrap;
  }
  .front-web .web-core { color: var(--brand-blue); }

  /* Back */
  .back-wordmark {
    position: absolute; left: 0; right: 0; top: 128px;
    text-align: center; color: var(--white); font-weight: 700; line-height: 1;
  }
  .back-wordmark .line-main { display: block; font-size: 104px; letter-spacing: 4px; }
  .back-wordmark .line-sub { display: block; font-size: 30px; letter-spacing: 4px; margin-top: 14px; }

  .back-web {
    position: absolute; left: 60px; right: 60px; top: 370px;
    display: flex; align-items: center; gap: 16px;
    color: var(--white); font-size: 15px; white-space: nowrap;
  }
  .back-web .rule { flex: 1; height: 1px; background: rgba(255,255,255,0.85); }
</style>
</head>
<body>
<main class="canvas">

  <section class="card card-front" aria-label="Business card front">
    <div class="front-wordmark">
      <span class="mark-name">
        <span class="line-main">VELRAN</span>
        <span class="line-sub">GLOBAL COMPONENTS</span>
      </span>
      <span class="mark-square" aria-hidden="true"></span>
    </div>

    <div class="contact-block">
      <h1 class="person-name">DANIEL HARTWELL</h1>
      <p class="person-title">Founder &amp; CEO</p>

      <ul class="contact-list">
        <li>
          <svg viewBox="0 0 16 16" aria-hidden="true">
            <rect x="1" y="2" width="4" height="13" rx="1" fill="#0a7fc2"/>
            <rect x="6" y="3" width="9" height="12" rx="1" fill="#0a7fc2"/>
            <rect x="8" y="5" width="5" height="2" fill="#fff"/>
            <rect x="8" y="9" width="1.5" height="1.5" fill="#fff"/>
            <rect x="11" y="9" width="1.5" height="1.5" fill="#fff"/>
            <rect x="8" y="12" width="1.5" height="1.5" fill="#fff"/>
            <rect x="11" y="12" width="1.5" height="1.5" fill="#fff"/>
          </svg>
          <span>+ 041 555 01 23</span>
        </li>
        <li>
          <svg viewBox="0 0 16 16" aria-hidden="true">
            <rect x="4" y="1" width="9" height="14" rx="1.5" fill="#0a7fc2"/>
            <rect x="5.5" y="3" width="6" height="8" fill="#fff"/>
            <circle cx="8.5" cy="13" r="1" fill="#fff"/>
          </svg>
          <span>+ 0164 555 02 47</span>
        </li>
        <li>
          <svg viewBox="0 0 16 16" aria-hidden="true">
            <rect x="1" y="4" width="14" height="9" fill="#0a7fc2"/>
            <path d="M1 4 L8 9.5 L15 4" fill="none" stroke="#fff" stroke-width="1.2"/>
          </svg>
          <span>info@velrancomponents-example.co.uk</span>
        </li>
      </ul>

      <address class="address">
        17 Marlow Yard, Upper Heath,<br>
        Warwick, CV31 8QL,<br>
        United Kingdom
      </address>
    </div>

    <p class="front-web">www.<span class="web-core">velrancomponents-example</span>.co.uk</p>
  </section>

  <section class="card card-back" aria-label="Business card back">
    <div class="back-wordmark">
      <span class="line-main">VELRAN</span>
      <span class="line-sub">GLOBAL COMPONENTS</span>
    </div>
    <div class="back-web">
      <span class="rule"></span>
      <span>www.velrancomponents-example.co.uk</span>
      <span class="rule"></span>
    </div>
  </section>

</main>
</body>
</html>
```